Business Card Design needed - Something Awesome!

Need a business card designed. Company is "Marlowe Advisory" we do consulting and also have sales automation technology.
I'm going to use thick stock or metal, something really nice... I was thinking about a QR Code on the back that would just upload my contact info to the persons contact, etc -

This is a Strategy Company with a tech feel. I'm open to ideas but really want this to be nice!

I need a template that should include:

Name | Position or Title
D: 415.902.3376
www.marloweadvisory.example

I'm going to attach my contact so you can use that one, I need to get this printed.

Target Market(s)

Small to mid size customers, Entrepreneurs etc.

Industry/Entity Type

Consulting, Tech, Private Equity.

Contact Information for Business Card

Name, Phone, Maybe email, URL

Font styles to use
Sans Serif

Colors

Designer to choose only greyscale colors for use in the design.

Requirements
Must have
• Fresh, Clean, stand out from the crowd - will be on thick stock or metal.
Nice to have
• Clean, simple yet impactful.
Should not have
• Not cartoonish

```html
<!DOCTYPE html>
<html lang="en">
<head>
<meta charset="utf-8">
<title>Marlowe Advisory — Business Card</title>
<link rel="stylesheet" href="https://fonts.googleapis.com/css2?family=Montserrat:wght@400;500;700&display=swap">
<style>
  :root {
    --backdrop: #2b2b2b;
    --card: #161616;
    --gloss: #3c3c3c;
    --white: #ffffff;
    --muted: #9a9a9a;
    --rule: #5a5a5a;
  }
  * { box-sizing: border-box; margin: 0; padding: 0; }
  html, body {
    width: 1200px; height: 1040px; overflow: hidden;
    background: var(--backdrop);
    font-family: "Montserrat", sans-serif;
  }
  .stage {
    width: 1200px; height: 1040px;
    display: flex; flex-direction: column; align-items: center; justify-content: center;
    gap: 70px;
  }
  .card {
    width: 735px; height: 420px;
    background: var(--card);
    border-radius: 0 90px 0 90px;
    position: relative;
    box-shadow: 0 10px 30px rgba(0,0,0,.45);
  }
  .card--front { display: flex; align-items: center; justify-content: center; }
  .wordmark {
    font-weight: 500; letter-spacing: 2px; line-height: 1;
  }
  .card--front .wordmark { font-size: 76px; color: var(--gloss); }
  .card--back { display: flex; align-items: center; }
  .card--back .wordmark {
    font-size: 52px; color: var(--white);
    width: 355px; text-align: center; padding-left: 40px;
  }
  .divider {
    width: 1px; height: 215px; background: var(--rule); margin: 0 30px 0 10px;
  }
  .details { color: var(--muted); }
  .person-name { color: var(--white); font-weight: 700; font-size: 22px; letter-spacing: 1px; }
  .person-title { font-size: 18px; font-weight: 500; margin-bottom: 22px; }
  .contact-list { list-style: none; }
  .contact-list li {
    display: flex; align-items: center; gap: 10px;
    font-size: 17px; font-weight: 500; line-height: 1.7;
  }
  .contact-list svg { width: 18px; height: 18px; flex: none; }
</style>
</head>
<body>
<main class="stage">
  <section class="card card--front" aria-label="Card front">
    <span class="wordmark">MARLOWE</span>
  </section>

  <section class="card card--back" aria-label="Card back">
    <span class="wordmark">MARLOWE</span>
    <span class="divider"></span>
    <div class="details">
      <p class="person-name">DANIEL OKAFOR</p>
      <p class="person-title">Managing Director</p>
      <ul class="contact-list">
        <li>
          <svg viewBox="0 0 24 24" fill="#ffffff" aria-hidden="true"><path d="M6.6 10.8a15.1 15.1 0 0 0 6.6 6.6l2.2-2.2a1 1 0 0 1 1-.25 11.4 11.4 0 0 0 3.6.57 1 1 0 0 1 1 1V20a1 1 0 0 1-1 1A17 17 0 0 1 3 4a1 1 0 0 1 1-1h3.5a1 1 0 0 1 1 1c0 1.25.2 2.45.57 3.57a1 1 0 0 1-.25 1z"/></svg>
          415.902.3376
        </li>
        <li>
          <svg viewBox="0 0 24 24" fill="none" stroke="#ffffff" stroke-width="2" aria-hidden="true"><rect x="2" y="5" width="20" height="14"/><path d="M2 5l10 8 10-8"/></svg>
          info@marloweadvisory.example
        </li>
        <li>
          <svg viewBox="0 0 24 24" fill="none" stroke="#ffffff" stroke-width="1.6" aria-hidden="true"><circle cx="12" cy="12" r="10"/><path d="M2 12h20M12 2c3 3 3 17 0 20M12 2c-3 3-3 17 0 20M4 7h16M4 17h16"/></svg>
          www.marloweadvisory.example
        </li>
      </ul>
    </div>
  </section>
</main>
</body>
</html>
```